Fresh, modern, fun business card for pediatric dental practice

Need a business card for fresh, modern, fun pediatric dental practice

Clean look that matches our website's font and colors

We prefer the look of curved corners on business cards

Target Market(s)

parents (mothers) of young children, professionals, mid-high class

Industry/Entity Type

Dental

Contact Information for Business Card

Maplebrook Pediatric Dentistry
482 Quarry Lane
Suite 517
Elmridge, PA 17690
717.555.0193
www.maplebrookkidsdental.example

Mei-Ran Tsai, DMD
Corinne Walbeck, DMD
(we are working on our email address, but we would like that on the card as well)

Font styles to use
Sans Serif

Requirements
Must have
• All info; we would also like to make cards for individual staff members
• colors from our website and color palatte, attatched
• use same font and design as website for branding
Nice to have
• clean, simple card that has a pop of color
• we would like to see a few designs with our tag line "where smiles get brighter"
• we are not sure if we want to have it on there or not
• we would like to see a few designs incorporating the ribbon graphic on our website where the word WELCOME is

```html
<!DOCTYPE html>
<html lang="en">
<head>
<meta charset="utf-8">
<title>Maplebrook Pediatric Dentistry – Business Card</title>
<link rel="stylesheet" href="https://fonts.googleapis.com/css2?family=Fira+Sans:wght@300;400;600;700&family=Roboto:wght@400&display=swap">
<style>
  :root {
    --backdrop: #c4c4c4;
    --plum: #4a2c4a;
    --gold: #e2a21a;
    --magenta: #b7287c;
    --paper: #f3f3f3;
    --ink-light: #ece6ec;
    --card-radius: 14px;
  }
  * { box-sizing: border-box; margin: 0; padding: 0; }
  html, body { width: 1200px; height: 576px; overflow: hidden; }
  body {
    background: var(--backdrop);
    position: relative;
    font-family: "Roboto", Arial, sans-serif;
  }
  .card {
    position: absolute;
    top: 138px;
    width: 484px;
    height: 294px;
    border-radius: var(--card-radius);
    background: var(--plum);
    overflow: hidden;
    box-shadow: 0 3px 8px rgba(0,0,0,0.25);
  }
  .card--front { left: 82px; }
  .card--back { left: 602px; }

  /* Front */
  .brand-mark {
    position: absolute;
    left: 50%;
    top: 66px;
    width: 44px;
    height: 44px;
    margin-left: -22px;
    border-radius: 50%;
    border: 3px solid var(--gold);
  }
  .brand-name {
    position: absolute;
    left: 0; right: 0;
    top: 126px;
    text-align: center;
    font-family: "Fira Sans", Arial, sans-serif;
    font-weight: 600;
    color: var(--gold);
    line-height: 1;
  }
  .brand-name__main { display: block; font-size: 44px; letter-spacing: 1px; }
  .brand-name__sub {
    display: block;
    font-size: 22px;
    font-weight: 400;
    letter-spacing: 1.5px;
    margin-top: 4px;
    color: var(--ink-light);
  }
  .front-web {
    position: absolute;
    left: 0; right: 0;
    top: 267px;
    display: flex;
    justify-content: center;
    align-items: center;
    gap: 18px;
    font-size: 11.5px;
    color: var(--ink-light);
    letter-spacing: 0.4px;
  }
  .front-web__domain { color: var(--gold); }
  .front-web__rule {
    width: 56px; height: 2px;
    background: linear-gradient(90deg, transparent, var(--magenta) 40%, var(--magenta) 60%, transparent);
  }

  /* Back */
  .back-shape { position: absolute; inset: 0; }
  .doctor-name {
    position: absolute;
    left: 21px; top: 31px;
    font-family: "Fira Sans", Arial, sans-serif;
    font-weight: 700;
    font-size: 17px;
    color: var(--gold);
  }
  .practice-name {
    position: absolute;
    left: 21px; top: 156px;
    font-family: "Fira Sans", Arial, sans-serif;
    font-weight: 700;
    font-size: 15px;
    color: var(--gold);
  }
  .address {
    position: absolute;
    left: 21px; top: 181px;
    font-size: 12px;
    line-height: 16px;
    color: var(--ink-light);
    font-style: normal;
  }
  .contact-list {
    position: absolute;
    left: 21px; top: 222px;
    list-style: none;
    font-size: 12px;
    line-height: 16px;
    color: var(--ink-light);
  }
  .contact-list li { display: flex; align-items: center; gap: 8px; }
  .contact-list svg { width: 10px; height: 10px; fill: var(--gold); flex: none; }
  .vertical-brand {
    position: absolute;
    left: 420px;
    top: 147px;
    transform: translate(-50%, -50%) rotate(-90deg);
    white-space: nowrap;
    font-family: "Fira Sans", Arial, sans-serif;
    font-weight: 600;
    color: var(--gold);
    line-height: 1;
    text-align: center;
  }
  .vertical-brand__main { display: block; font-size: 34px; letter-spacing: 1px; }
  .vertical-brand__sub {
    display: block;
    font-size: 17px;
    font-weight: 300;
    letter-spacing: 1px;
    margin-top: 4px;
    color: var(--magenta);
  }
  .back-mark {
    position: absolute;
    left: 340px; top: 131px;
    width: 32px; height: 32px;
    border-radius: 50%;
    border: 2.5px solid var(--gold);
  }
</style>
</head>
<body>

<section class="card card--front" aria-label="Card front">
  <span class="brand-mark" aria-hidden="true"></span>
  <h1 class="brand-name">
    <span class="brand-name__main">maplebrook</span>
    <span class="brand-name__sub">pediatric dentistry</span>
  </h1>
  <p class="front-web">
    <span class="front-web__rule"></span>
    <span>www.<span class="front-web__domain">maplebrookkidsdental</span>.example</span>
    <span class="front-web__rule"></span>
  </p>
</section>

<section class="card card--back" aria-label="Card back">
  <svg class="back-shape" viewBox="0 0 484 294" preserveAspectRatio="none" aria-hidden="true">
    <path d="M346 0 Q250 150 334 294 L484 294 L484 0 Z" fill="var(--paper)"/>
    <path d="M346 0 L364 0 Q294 90 306 200 Q284 95 346 0 Z" fill="var(--magenta)"/>
  </svg>

  <h2 class="doctor-name">Corinne Walbeck, DMD</h2>

  <h3 class="practice-name">Maplebrook Pediatric Dentistry</h3>
  <address class="address">
    482 Quarry Lane<br>
    Suite 517 Elmridge, PA 17690
  </address>
  <ul class="contact-list">
    <li><svg viewBox="0 0 10 10"><path d="M1 3.5C1 2 2.5 1 5 1s4 1 4 2.5L7.2 4.2 6.8 3H3.2L2.8 4.2Z M2.5 5h5l1 4h-7Z"/></svg>717.555.0193</li>
    <li><svg viewBox="0 0 10 10"><path d="M0 2h10v1L5 6 0 3Z M0 4l5 3 5-3v4H0Z"/></svg>name@maplebrookkidsdental.example</li>
    <li><svg viewBox="0 0 10 10"><circle cx="5" cy="5" r="4.5"/></svg>www.maplebrookkidsdental.example</li>
  </ul>

  <span class="back-mark" aria-hidden="true"></span>
  <p class="vertical-brand">
    <span class="vertical-brand__main">maplebrook</span>
    <span class="vertical-brand__sub">pediatric dentistry</span>
  </p>
</section>

</body>
</html>
```